New Mechanical Maintenance business needs website

New Mechanical Maintenance business in Perth Western Australia needs a nice and easy to navigate website. Showing what we do and how we can be the right fit for other small to medium size business by offering personalized service from our highly skilled team. We deal with both fixed plant repairs like food and chemical processing facilities to heavy equipment like drill rigs, Large boats and earthmoving equipment.

Target Market(s)

Small to medium business to offer personalized services/packages

Industry/Entity Type

e deal with both fixed plant repairs like food and chemical processing facilities to heavy equipment like drill rigs, Large boats and earthmoving equipment.

Coding

Coded - Design and coding required

Number of Pages Required

4 page

Font styles to use
Serif

Colors
0054AA
0677BA
7BADD7
CADEEF
E8F1F8

Requirements
Must have
• A website that is easy to navigate but covers off on the range of services/maintenance we can provide

```html
<!DOCTYPE html>
<html lang="en">
<head>
<meta charset="utf-8">
<title>KVR Maintenance</title>
<link href="https://fonts.googleapis.com/css2?family=Lora:wght@400;500;600&display=swap" rel="stylesheet">
<style>
:root{
  --slate:#56688c;
  --ink:#1f2430;
  --band:#e9eef7;
  --rule:#cfd6e3;
  --line:#50545c;
  --white:#ffffff;
  --black:#000000;
}
*{margin:0;padding:0;box-sizing:border-box}
html,body{width:1200px;height:3831px;overflow:hidden}
body{position:relative;font-family:"Lora",Georgia,serif;color:var(--ink);background:var(--white)}
.abs{position:absolute}
a{text-decoration:none}

/* header */
.header{left:0;top:0;width:1200px;height:97px;background:var(--white);z-index:3}
.nav-link{position:absolute;top:39px;white-space:nowrap;font-size:15px;font-weight:500;color:var(--slate);letter-spacing:.3px}
.search{left:1061px;top:37px;width:28px;height:28px;border-radius:50%;background:var(--slate)}
.brand-badge{left:112px;top:-10px;width:142px;height:142px;border-radius:50%;background:var(--white);z-index:4;display:flex;flex-direction:column;align-items:center;justify-content:center;color:var(--slate);font-weight:600;font-size:14px;letter-spacing:1px;line-height:1.35;text-align:center}

/* hero */
.hero{left:0;top:97px;width:1200px;height:584px;background:linear-gradient(90deg,#6d7fa3 0%,#8596b8 35%,#8a8f99 60%,#5a5f66 100%)}
.hero-copy{left:112px;top:246px;width:520px;color:var(--white)}
.hero-welcome{font-size:26px;font-weight:500;letter-spacing:.5px;line-height:34px}
.hero-title{margin-top:20px;font-size:44px;font-weight:500;letter-spacing:.5px;line-height:50px}
.hero-lede{margin-top:24px;font-size:16px;line-height:36px}
.btn-light{left:112px;top:518px;width:194px;height:50px;border-radius:25px;background:var(--white);color:var(--slate);font-size:16px;font-weight:500;display:flex;align-items:center;justify-content:center}
.drop{left:534px;top:632px;width:132px;height:132px;border-radius:50%;background:var(--white);z-index:2}
.chev{position:absolute;left:50%;top:38px;width:12px;height:12px;border-right:2px solid var(--slate);border-bottom:2px solid var(--slate);transform:translateX(-50%) rotate(45deg)}

/* what we do */
.about-disc{left:128px;top:793px;width:436px;height:436px;border-radius:50%;background:var(--slate)}
.about-photo{left:220px;top:872px;width:280px;height:280px;border-radius:50%;background:linear-gradient(135deg,#3c6aa8,#9aa6b8 55%,#5a4f6b)}
.h2{font-size:34px;font-weight:500;color:var(--slate);letter-spacing:.5px;line-height:40px}
.about-h{left:622px;top:768px}
.about-p{left:623px;top:826px;width:480px;font-size:16px;line-height:36px;white-space:nowrap}
.btn-dark{left:623px;top:1175px;width:161px;height:50px;border-radius:25px;background:var(--slate);color:var(--white);font-size:16px;font-weight:500;display:flex;align-items:center;justify-content:center}

/* why choose us */
.band{left:0;top:1322px;width:1200px;height:662px;background:var(--band)}
.notch{left:151px;top:1322px;width:0;height:0;border-left:20px solid transparent;border-right:20px solid transparent;border-top:28px solid var(--white)}
.why-h{left:0;width:1200px;top:1380px;text-align:center}
.why-list{left:120px;top:1472px;width:313px;height:340px}
.why-item{position:absolute;left:0;height:45px;width:313px;display:flex;align-items:center;font-size:21px;font-weight:500;color:var(--slate);letter-spacing:.5px}
.why-item .ico{width:30px;height:30px;margin-left:3px;margin-right:31px;border-radius:50%;border:5px solid var(--slate);flex:none}
.why-item.active{background:linear-gradient(90deg,rgba(86,104,140,0) 56%,rgba(86,104,140,.4) 75%,var(--slate) 100%)}
.why-rule{left:432px;top:1475px;width:2px;height:332px;background:var(--rule)}
.why-sub{left:488px;top:1498px;font-size:19px;font-weight:500;color:var(--slate)}
.why-p{left:488px;top:1551px;width:600px;font-size:16px;line-height:36px;white-space:nowrap}
.why-photo{left:488px;top:1662px;width:572px;height:241px;border-radius:12px;background:linear-gradient(100deg,#d9b83c,#e8cb55 40%,#3a3a3a 60%,#c9a736)}

/* services */
.services-h{left:0;width:1200px;top:2068px;text-align:center}
.services{left:0;top:2150px}
.svc-label{font-family:"Lora",Georgia,serif;font-size:17px;font-weight:500;fill:#3d4250;letter-spacing:.5px}

/* gallery */
.gallery-h{left:0;width:1200px;top:2700px;text-align:center}
.shot{border-radius:10px}

/* footer */
.footer{left:0;top:3413px;width:1200px;height:418px;background:var(--black)}
.up{left:534px;top:3330px;width:132px;height:132px;border-radius:50%;background:var(--white);z-index:2}
.up .chev{top:auto;bottom:36px;transform:translateX(-50%) rotate(-135deg)}
.foot-badge{left:548px;top:3497px;width:104px;height:104px;border-radius:50%;border:2px solid var(--white);display:flex;flex-direction:column;align-items:center;justify-content:center;color:var(--white);font-size:12px;font-weight:600;letter-spacing:.5px;line-height:1.4;text-align:center}
.foot-link{position:absolute;top:3651px;color:var(--white);font-size:16px;font-weight:500;white-space:nowrap}
.contact{top:3705px;display:flex;align-items:center;color:var(--white);font-size:12px;font-weight:600;white-space:nowrap}
.contact .ring{width:40px;height:40px;border-radius:50%;border:1.5px solid var(--white);display:flex;align-items:center;justify-content:center;margin-right:18px;flex:none}
.copy{left:0;width:1200px;top:3770px;text-align:center;color:var(--white);font-size:12px;font-weight:600}
</style>
</head>
<body>

<header class="abs header">
  <a class="nav-link" href="#" style="left:391px">HOME</a>
  <a class="nav-link" href="#" style="left:475px">WHAT WE DO</a>
  <a class="nav-link" href="#" style="left:622px">WHY CHOOSE US</a>
  <a class="nav-link" href="#" style="left:798px">GALLERY</a>
  <a class="nav-link" href="#" style="left:906px">CONTACT US</a>
  <div class="abs search">
    <svg width="28" height="28" viewBox="0 0 28 28"><circle cx="13" cy="13" r="5" fill="none" stroke="#fff" stroke-width="2"/><line x1="16.5" y1="16.5" x2="20" y2="20" stroke="#fff" stroke-width="2"/></svg>
  </div>
</header>
<div class="abs brand-badge">KVR<br>MAINTENANCE</div>

<section class="abs hero" role="img" aria-label="Senior technician in hard hat checking a notebook beside factory machinery"></section>
<div class="abs hero-copy">
  <p class="hero-welcome">WELCOME TO</p>
  <h1 class="hero-title">KVR MAINTENANCE</h1>
  <p class="hero-lede">Sed ut perspiciatis unde omnis iste natus error sit<br>voluptatem accusantium doloremque<br>laudantium, totam rem aperiam</p>
</div>
<a class="abs btn-light" href="#">GET STARTED NOW</a>
<div class="abs drop"><span class="chev"></span></div>

<section>
  <div class="abs about-disc"></div>
  <div class="abs about-photo" role="img" aria-label="Engineer operating a milling machine in a workshop"></div>
  <h2 class="abs h2 about-h">WHAT WE DO</h2>
  <p class="abs about-p">Lorem ipsum dolor sit amet, consectetur adipiscing elit,<br>sed do eiusmod tempor incididunt ut labore et dolore<br>magna aliqua. Ut enim ad minim veniam, quis nostrud<br>exercitation ullamco laboris nisi ut aliquip ex ea<br>commodo consequat. Duis aute irure dolor in<br>reprehenderit in voluptate velit esse cillum dolore eu<br>fugiat nulla pariatur. Excepteur sint occaecat cupidatat<br>non proident, sunt in culpa qui officia deserunt mollit<br>anim id est laborum.</p>
  <a class="abs btn-dark" href="#">LEARN MORE</a>
</section>

<section>
  <div class="abs band"></div>
  <div class="abs notch"></div>
  <h2 class="abs h2 why-h">WHY CHOOSE US</h2>
  <div class="abs why-list">
    <div class="why-item" style="top:0"><span class="ico"></span>LOREM IPSUM</div>
    <div class="why-item" style="top:68px"><span class="ico"></span>LOREM IPSUM</div>
    <div class="why-item active" style="top:137px"><span class="ico"></span>LOREM IPSUM</div>
    <div class="why-item" style="top:205px"><span class="ico"></span>LOREM IPSUM</div>
    <div class="why-item" style="top:274px"><span class="ico"></span>LOREM IPSUM</div>
  </div>
  <div class="abs why-rule"></div>
  <h3 class="abs why-sub">LOREM IPSUM</h3>
  <p class="abs why-p">Lorem ipsum dolor sit amet, consectetur adipiscing elit, sed do eiusmod<br>tempor incididunt ut labore et dolore magna aliqua.</p>
  <div class="abs why-photo" role="img" aria-label="Mechanic servicing hydraulic lines on yellow heavy equipment"></div>
</section>

<section>
  <h2 class="abs h2 services-h">OUR SERVICES</h2>
  <svg class="abs services" width="1200" height="500" viewBox="0 0 1200 500">
    <defs>
      <circle id="ring" r="92" fill="none" stroke="#50545c" stroke-width="2.5"/>
    </defs>
    <g stroke="#50545c" stroke-width="2.5">
      <line x1="300" y1="241" x2="490" y2="241"/>
      <line x1="710" y1="241" x2="897" y2="241"/>
      <line x1="479" y1="166" x2="506" y2="183"/>
      <line x1="721" y1="166" x2="694" y2="183"/>
      <line x1="479" y1="316" x2="506" y2="299"/>
      <line x1="721" y1="316" x2="694" y2="299"/>
    </g>
    <circle cx="600" cy="241" r="110" fill="#fff" stroke="#50545c" stroke-width="1.5" stroke-dasharray="5 4"/>
    <g fill="#50545c">
      <circle cx="308" cy="241" r="6"/><circle cx="892" cy="241" r="6"/>
      <circle cx="479" cy="166" r="6"/><circle cx="721" cy="166" r="6"/>
      <circle cx="479" cy="316" r="6"/><circle cx="721" cy="316" r="6"/>
      <circle cx="506" cy="183" r="4"/><circle cx="694" cy="183" r="4"/>
      <circle cx="506" cy="299" r="4"/><circle cx="694" cy="299" r="4"/>
    </g>
    <circle cx="600" cy="241" r="86" fill="#56688c"/>
    <text x="600" y="238" text-anchor="middle" fill="#fff" font-family="Lora, Georgia, serif" font-size="14" font-weight="600" letter-spacing="1">KVR</text>
    <text x="600" y="258" text-anchor="middle" fill="#fff" font-family="Lora, Georgia, serif" font-size="14" font-weight="600" letter-spacing="1">MAINTENANCE</text>

    <g fill="none" stroke="#56688c" stroke-width="7">
      <path d="M336 53 A92 92 0 0 1 466 53"/><path d="M466 183 A92 92 0 0 1 336 183"/>
      <path d="M731 53 A92 92 0 0 1 861 53"/><path d="M861 183 A92 92 0 0 1 731 183"/>
      <path d="M143 176 A92 92 0 0 1 273 176"/><path d="M273 306 A92 92 0 0 1 143 306"/>
      <path d="M924 176 A92 92 0 0 1 1054 176"/><path d="M1054 306 A92 92 0 0 1 924 306"/>
      <path d="M336 299 A92 92 0 0 1 466 299"/><path d="M466 429 A92 92 0 0 1 336 429"/>
      <path d="M731 299 A92 92 0 0 1 861 299"/><path d="M861 429 A92 92 0 0 1 731 429"/>
    </g>
    <use href="#ring" x="401" y="118"/><use href="#ring" x="796" y="118"/>
    <use href="#ring" x="208" y="241"/><use href="#ring" x="989" y="241"/>
    <use href="#ring" x="401" y="364"/><use href="#ring" x="796" y="364"/>

    <g fill="#56688c">
      <circle cx="311" cy="116" r="31"/><circle cx="889" cy="116" r="31"/>
      <circle cx="119" cy="241" r="31"/><circle cx="1081" cy="241" r="31"/>
      <circle cx="311" cy="364" r="31"/><circle cx="889" cy="364" r="31"/>
    </g>
    <g stroke="#fff" stroke-width="3" fill="none" stroke-linecap="round" stroke-linejoin="round">
      <!-- wrench -->
      <path d="M300 127 L316 111 M314 104 a6 6 0 1 0 8 8"/>
      <!-- drill rig mast -->
      <path d="M889 100 L880 130 M889 100 L898 130 M884 116 h10 M878 130 h22"/>
      <!-- factory -->
      <path d="M105 253 v-16 l8 -5 v5 l8 -5 v5 l8 -5 v21 z M131 253 v-26"/>
      <!-- earthmover -->
      <path d="M1066 250 h22 v-10 h-14 v10 M1088 244 l8 -8 l4 6"/>
      <circle cx="1072" cy="252" r="2"/><circle cx="1084" cy="252" r="2"/>
      <!-- boat -->
      <path d="M297 366 h28 l-5 9 h-18 z M311 366 v-16 l8 10 h-8"/>
      <!-- hydraulic drop -->
      <path d="M889 350 c-7 10 -10 14 -10 18 a10 10 0 0 0 20 0 c0 -4 -3 -8 -10 -18z"/>
    </g>

    <g class="svc-label" text-anchor="middle">
      <text x="412" y="110">FIXED PLANT</text><text x="412" y="140">REPAIRS</text>
      <text x="796" y="110">DRILL</text><text x="796" y="140">RIGS</text>
      <text x="221" y="234">PROCESSING</text><text x="221" y="264">PLANTS</text>
      <text x="982" y="234">EARTHMOVING</text><text x="982" y="264">PLANT</text>
      <text x="414" y="357">MARINE</text><text x="414" y="387">VESSELS</text>
      <text x="794" y="357">HYDRAULIC</text><text x="794" y="387">SYSTEMS</text>
    </g>
  </svg>
</section>

<section>
  <h2 class="abs h2 gallery-h">OUR GALLERY</h2>
  <div class="abs shot" style="left:0;top:2806px;width:168px;height:308px;background:linear-gradient(180deg,#8a6a3a,#c4873a 50%,#1d2a3a)" role="img" aria-label="Offshore oil platform at dusk"></div>
  <div class="abs shot" style="left:0;top:3132px;width:168px;height:184px;background:linear-gradient(160deg,#3d6b8a,#c06a4a 50%,#2a4f6b)" role="img" aria-label="Container ship seen from above"></div>
  <div class="abs shot" style="left:181px;top:2833px;width:399px;height:413px;background:linear-gradient(110deg,#d9b83c,#e6c955 35%,#3a3a3a 60%,#b9972e)" role="img" aria-label="Mechanic servicing hydraulic lines on heavy equipment"></div>
  <div class="abs shot" style="left:595px;top:2922px;width:398px;height:413px;background:linear-gradient(180deg,#3f74c2,#9dbfe6 45%,#b5603a 75%,#c98a5a)" role="img" aria-label="Drill rig on red earth under blue sky"></div>
  <div class="abs shot" style="left:1008px;top:2806px;width:192px;height:186px;background:linear-gradient(170deg,#5f86a8,#2f5775 60%,#c24a3a)" role="img" aria-label="Loaded cargo ship at sea"></div>
  <div class="abs shot" style="left:1008px;top:3010px;width:192px;height:306px;background:linear-gradient(160deg,#a4512e,#5a3a28 50%,#2a2520)" role="img" aria-label="Close-up of drilling equipment in soil"></div>
</section>

<footer>
  <div class="abs footer"></div>
  <div class="abs up"><span class="chev"></span></div>
  <div class="abs foot-badge">KVR<br>MAINTENANCE</div>
  <a class="foot-link" href="#" style="left:288px">HOME</a>
  <a class="foot-link" href="#" style="left:373px">WHAT WE DO</a>
  <a class="foot-link" href="#" style="left:520px">WHY CHOOSE US</a>
  <a class="foot-link" href="#" style="left:696px">GALLERY</a>
  <a class="foot-link" href="#" style="left:804px">CONTACT US</a>
  <div class="abs contact" style="left:288px">
    <span class="ring"><svg width="16" height="18" viewBox="0 0 16 18"><path d="M8 17 C3 11 2 9 2 7 a6 6 0 0 1 12 0 c0 2 -1 4 -6 10z" fill="#fff"/><circle cx="8" cy="7" r="2.2" fill="#000"/></svg></span>
    14, KVR MAINTENANCE, LOREM IPSUM, 061 204
  </div>
  <div class="abs contact" style="left:754px">
    <span class="ring"><svg width="16" height="16" viewBox="0 0 16 16"><path d="M3 1 l3 0 l1 4 l-2 1.5 a9 9 0 0 0 4.5 4.5 l1.5 -2 l4 1 l0 3 a2 2 0 0 1 -2 2 a13 13 0 0 1 -12 -12 a2 2 0 0 1 2 -2z" fill="#fff"/></svg></span>
    +1 555 010 0199
  </div>
  <p class="abs copy">@2024 COPYRIGHTS - ALL RIGHTS RESERVED</p>
</footer>

</body>
</html>
```